Calloway Metal Recyclers - www.callowayrecyclers-example.com.au

I've just rebranded my business and thought what better way to continue with this than getting a website.
It is going to be fairly basic for now. I've attached quite a few images, feel free to use whichever you like.
And pages description is also attached in a .doc file.
Updates

Hi, this is my first time having a website. I am open to anything and trust the experience and ideas you can bring forward. I will look at extending the deadline so I can take my time to give feedback as needed! Thank you all.

Target Market(s)

Mining and industrial and commercial sectors

Coding

Coded - Design and coding required

Number of Pages Required

5+ page

Requirements
Must have
• Logo/Phone number at the top of every page. "Scrap Metal Specialists" tag line at the top of every page.
Nice to have
• Top Navigation.

```html
<!DOCTYPE html>
<html lang="en">
<head>
<meta charset="utf-8">
<title>Calloway Metal Recyclers</title>
<link href="https://fonts.googleapis.com/css2?family=Oswald:wght@400;500;600&family=Roboto:wght@400;500&display=swap" rel="stylesheet">
<style>
:root{
  --navy:#1b3a6e;
  --navy-deep:#142c57;
  --grey:#6d6e71;
  --ink:#222;
  --white:#fff;
  --black:#000;
  --soft:#dfe3ea;
}
*{box-sizing:border-box;margin:0;padding:0}
html,body{width:1200px;height:2977px;overflow:hidden}
body{position:relative;font-family:'Roboto',sans-serif;color:var(--ink);background:var(--white)}
.abs{position:absolute}
.oswald{font-family:'Oswald',sans-serif}

/* header */
.brand{left:112px;top:18px;width:200px;font-family:'Oswald',sans-serif;font-weight:600;color:var(--navy);text-align:center;line-height:1}
.brand .b1{font-size:38px;letter-spacing:1px}
.brand .b2{font-size:19px;margin-top:4px}
.brand .b3{font-size:18px;margin-top:2px}
.contact-item{top:16px;display:flex;align-items:center;gap:14px}
.contact-item .ico{width:46px;height:46px;border-radius:50%;background:var(--navy);display:flex;align-items:center;justify-content:center}
.contact-item .lbl{font-family:'Oswald',sans-serif;font-size:15px;color:var(--ink)}
.contact-item .val{font-size:15px;color:var(--grey);margin-top:4px}
.divider{top:30px;width:1px;height:20px;background:#ccc}
.socials-top{left:982px;top:31px;display:flex;gap:14px}
.socials-top span{width:16px;height:16px;border-radius:3px;background:var(--navy)}
.nav{left:402px;top:98px;display:flex;gap:34px;font-size:15px}
.nav a{color:var(--ink);text-decoration:none}
.nav a.active{color:var(--navy)}
.login{left:985px;top:83px;width:104px;height:49px;border:2px solid var(--navy);border-radius:3px;font-family:'Oswald',sans-serif;font-weight:500;color:var(--navy);font-size:15px;display:flex;align-items:center;justify-content:center}

/* hero */
.hero{left:0;top:147px;width:1200px;height:686px;background:linear-gradient(100deg,#1b3a6e 0%,#2a4572 35%,#5b5240 65%,#8a7440 85%,#3b3a35 100%)}
.hero-shape{left:0;top:740px}
.hero-text{left:112px;top:318px;color:var(--white);font-family:'Oswald',sans-serif}
.hero-text .t1{font-size:50px;font-weight:400;line-height:1}
.hero-text .t2{font-size:71px;font-weight:600;line-height:78px;margin-top:14px}
.hero-btn{left:114px;top:566px;width:112px;height:44px;border:2px solid var(--white);border-radius:3px;color:var(--white);font-family:'Oswald',sans-serif;font-weight:500;font-size:15px;display:flex;align-items:center;justify-content:center}
.dots{left:575px;top:736px;display:flex;align-items:center;gap:6px}
.dots span{width:10px;height:10px;border-radius:50%;background:var(--white)}
.dots span.on{width:18px;height:18px;background:none;border:3px solid var(--white)}

/* section titles */
.sec-title{left:0;width:1200px;text-align:center;font-family:'Oswald',sans-serif;font-size:38px;font-weight:600}
.sec-title .light{color:var(--grey)}
.sec-title .dark{color:var(--navy)}

/* services */
.svc{top:964px;width:308px;height:260px;overflow:hidden}
.svc .photo{position:absolute;inset:0}
.svc .cap{position:absolute;left:0;bottom:0;width:270px;height:44px;background:var(--white);clip-path:polygon(0 0,88% 0,100% 100%,0 100%);font-family:'Oswald',sans-serif;font-size:17px;display:flex;align-items:center;padding-left:11px;gap:36px}
.svc.feature{background:var(--navy);color:var(--white);text-align:center;padding:38px 20px 0}
.svc.feature h3{font-family:'Oswald',sans-serif;font-weight:500;font-size:23px}
.svc.feature p{font-size:15.5px;line-height:26px;margin-top:14px}
.svc.feature .more{display:inline-block;margin-top:12px;font-family:'Oswald',sans-serif;font-weight:500;font-size:15px;text-decoration:underline}
.arrow-btn{top:1078px;width:34px;height:34px;border-radius:50%;border:1.5px solid var(--navy);display:flex;align-items:center;justify-content:center}

/* about */
.about{left:0;top:1317px;width:1200px;height:600px;background:linear-gradient(110deg,#cfd0d2 0%,#c9c2b6 40%,#d8dadd 70%,#c7cdd0 100%)}
.frame{border:2px solid var(--navy)}
.portrait{left:129px;top:1410px;width:361px;height:413px;background:linear-gradient(180deg,#d0d1d3,#a9abae)}
.about-text{left:610px;top:1455px;width:458px}
.about-text h2{font-family:'Oswald',sans-serif;font-size:38px;font-weight:600}
.about-text h4{font-size:21px;font-weight:500;color:var(--navy);margin-top:20px}
.about-text p{font-size:16px;line-height:28.5px;color:#444;margin-top:18px;text-align:justify}
.about-btn{display:inline-flex;margin-top:30px;width:118px;height:48px;background:var(--navy);color:var(--white);font-family:'Oswald',sans-serif;font-weight:500;font-size:15px;align-items:center;justify-content:center;border-radius:2px}

/* blog */
.post{top:2096px;width:312px}
.post .photo{width:312px;height:246px;clip-path:polygon(0 0,100% 0,100% 100%,0 100%)}
.post .date{position:absolute;left:23px;top:195px;width:128px;height:37px;background:var(--navy);color:var(--white);font-family:'Oswald',sans-serif;font-size:15px;display:flex;align-items:center;justify-content:center}
.post .mask{position:absolute;left:0;top:215px;width:282px;height:32px;background:var(--white)}
.post p{font-family:'Oswald',sans-serif;font-size:17px;line-height:30px;padding:6px 23px 0;color:#333}

/* footer */
.footer-shape{left:0;top:2545px}
.footer{left:0;top:2625px;width:1200px;height:352px;background:var(--black)}
.f-brand{left:112px;top:2712px;width:200px;font-family:'Oswald',sans-serif;font-weight:600;color:#8b8d90;text-align:center;line-height:1}
.f-brand .b1{font-size:38px;letter-spacing:1px}
.f-brand .b2{font-size:19px;margin-top:4px}
.f-brand .b3{font-size:18px;margin-top:2px}
.f-col h5{font-family:'Oswald',sans-serif;font-size:19px;font-weight:500;color:var(--white)}
.f-links{list-style:none;margin-top:16px}
.f-links li{color:var(--white);font-size:15px;line-height:26px}
.f-contact{margin-top:18px;color:var(--white);font-size:15px}
.f-contact div{display:flex;gap:14px;margin-bottom:12px;line-height:25px}
.f-contact svg{flex:none;margin-top:4px}
.newsletter{margin-top:22px;display:flex;width:225px;height:40px;background:var(--white);border-radius:4px;overflow:hidden}
.newsletter span{flex:1;padding:12px 14px;font-size:15px;color:#777}
.newsletter b{width:54px;background:var(--navy);display:flex;align-items:center;justify-content:center}
.f-social{display:flex;gap:11px;margin-top:28px;margin-left:29px}
.f-social span{width:41px;height:41px;border-radius:50%;background:var(--white)}
.copy{left:0;top:2924px;width:1200px;text-align:center;color:var(--white);font-size:15px}
</style>
</head>
<body>

<!-- header -->
<div class="abs brand">
  <div class="b1">CALLOWAY</div>
  <div class="b2">METAL RECYCLERS</div>
  <div class="b3">0455123987</div>
</div>
<div class="abs contact-item" style="left:458px">
  <div class="ico"><svg width="22" height="22" viewBox="0 0 24 24" fill="none" stroke="#fff" stroke-width="1.6"><path d="M5 3h4l2 5-2.5 1.5a11 11 0 0 0 6 6L16 13l5 2v4a2 2 0 0 1-2 2A16 16 0 0 1 3 5a2 2 0 0 1 2-2z"/></svg></div>
  <div><div class="lbl">Call us</div><div class="val">0455123987</div></div>
</div>
<div class="abs divider" style="left:623px"></div>
<div class="abs contact-item" style="left:648px">
  <div class="ico"><svg width="22" height="18" viewBox="0 0 24 18" fill="none" stroke="#fff" stroke-width="1.6"><rect x="1" y="1" width="22" height="16" rx="1"/><path d="M1 2l11 9 11-9"/></svg></div>
  <div><div class="lbl">Email</div><div class="val">dan@callowayrecyclers-example.com.au</div></div>
</div>
<div class="abs divider" style="left:952px"></div>
<div class="abs socials-top"><span></span><span></span><span></span><span></span></div>
<nav class="abs nav">
  <a class="active">HOME</a><a>ABOUT</a><a>SERVICES</a><a>ONLINE STORE</a><a>BLOG</a><a>CONTACT</a>
</nav>
<div class="abs login">LOG IN</div>

<!-- hero -->
<div class="abs hero" role="img" aria-label="Scrap yard at dusk with a large steel cable drum and machinery"></div>
<svg class="abs hero-shape" width="1200" height="94" viewBox="0 0 1200 94">
  <polygon points="0,80 985,23 1200,80 1200,94 0,94" fill="#fff"/>
  <polygon points="0,80 985,22 1200,82 1200,74 988,12 0,72" fill="#1b3a6e"/>
</svg>
<div class="abs hero-text">
  <div class="t1">WELCOME TO</div>
  <div class="t2">CALLOWAY METAL<br>RECYCLERS</div>
</div>
<div class="abs hero-btn">0455123987</div>
<div class="abs dots"><span></span><span class="on"></span><span></span></div>

<!-- services -->
<h2 class="abs sec-title" style="top:866px"><span class="light">OUR</span> <span class="dark">SERVICES</span></h2>
<div class="abs arrow-btn" style="left:57px"><svg width="10" height="14" viewBox="0 0 10 14" fill="none" stroke="#1b3a6e" stroke-width="1.6"><path d="M8 1L2 7l6 6"/></svg></div>
<div class="abs svc" style="left:112px">
  <div class="photo" role="img" aria-label="Large cut steel shaft from mining machinery" style="background:linear-gradient(135deg,#8a5a3a,#6b4a36 50%,#3d3a38)"></div>
  <div class="cap">Large mining machinery <svg width="18" height="12" viewBox="0 0 18 12" fill="none" stroke="#1b3a6e" stroke-width="1.8"><path d="M0 6h16M11 1l5 5-5 5"/></svg></div>
</div>
<div class="abs svc feature" style="left:446px">
  <h3>Heavy industrial equipment</h3>
  <p>Lorem ipsum dolor sit amet, consectetur adipiscing elit, sed do eiusmod tempor incididunt ut labore et dolore magna aliqua.</p>
  <span class="more">LEARN MORE</span>
</div>
<div class="abs svc" style="left:779px">
  <div class="photo" role="img" aria-label="Rusted truck tray in a scrap yard" style="background:linear-gradient(180deg,#8d98a6 0%,#6e7a6a 35%,#7a4a3a 65%,#6a5a4a 100%)"></div>
  <div class="cap">Scrap metal clean up <svg width="18" height="12" viewBox="0 0 18 12" fill="none" stroke="#1b3a6e" stroke-width="1.8"><path d="M0 6h16M11 1l5 5-5 5"/></svg></div>
</div>
<div class="abs arrow-btn" style="left:1106px"><svg width="10" height="14" viewBox="0 0 10 14" fill="none" stroke="#1b3a6e" stroke-width="1.6"><path d="M2 1l6 6-6 6"/></svg></div>

<!-- about -->
<div class="abs about" role="img" aria-label="Faded background of heavy scrap machinery"></div>
<div class="abs frame" style="left:120px;top:1403px;width:258px;height:248px;border-right:none;border-bottom:none"></div>
<div class="abs frame" style="left:265px;top:1660px;width:233px;height:170px;border-color:#8a8c90;border-left:none;border-top:none"></div>
<div class="abs portrait" role="img" aria-label="Portrait of the managing director in a dark suit"></div>
<div class="abs about-text">
  <h2><span style="color:var(--grey)">ABOUT</span> <span style="color:var(--navy)">ME</span></h2>
  <h4>Dan Hartley</h4>
  <p>I'm the managing director of Calloway Metal Processors. I have been in the scrap metal recycling industry longer than I haven't! I have 16 years' experience in everything scrap metal and I am very passionate about sustainable recycling</p>
  <span class="about-btn">LEARN MORE</span>
</div>

<!-- blog -->
<h2 class="abs sec-title" style="top:1997px"><span class="light">LATEST</span> <span class="dark">BLOG</span></h2>
<div class="abs" style="left:880px;top:2110px;width:320px;height:440px;background:linear-gradient(200deg,#dfe3ea,#fff 70%);clip-path:polygon(100% 0,100% 40%,40% 100%,10% 100%)"></div>
<div class="abs post" style="left:111px">
  <div class="photo" role="img" aria-label="Rusted steel castings on red earth" style="background:linear-gradient(135deg,#a04a22,#c2653a 50%,#7a3a1e)"></div>
  <div class="mask"></div><div class="date">18 Nov,2022</div>
  <p>Lorem ipsum dolor si a consectetur adipiscing elit, sed do eiusmo dolore magna aliqua</p>
</div>
<div class="abs post" style="left:444px">
  <div class="photo" role="img" aria-label="Large rusted gear ring on the ground" style="background:linear-gradient(135deg,#7a6650,#4a3a30 50%,#9a8a70)"></div>
  <div class="mask"></div><div class="date">18 Nov,2022</div>
  <p>Lorem ipsum dolor si a consectetur adipiscing elit, sed do eiusmo dolore magna aliqua</p>
</div>
<div class="abs post" style="left:776px">
  <div class="photo" role="img" aria-label="Yellow hydraulic machinery part for scrap" style="background:linear-gradient(135deg,#5a5a5a,#c8a030 50%,#6a6660)"></div>
  <div class="mask"></div><div class="date">18 Nov,2022</div>
  <p>Lorem ipsum dolor si a consectetur adipiscing elit, sed do eiusmo dolore magna aliqua</p>
</div>

<!-- footer -->
<svg class="abs footer-shape" width="1200" height="82" viewBox="0 0 1200 82">
  <polygon points="0,75 210,5 1200,80 1200,82 0,82" fill="#000"/>
  <polygon points="0,68 212,0 1200,70 1200,80 210,12 0,80" fill="#1b3a6e"/>
</svg>
<div class="abs footer"></div>
<div class="abs f-brand">
  <div class="b1">CALLOWAY</div>
  <div class="b2">METAL RECYCLERS</div>
  <div class="b3">0455123987</div>
</div>
<div class="abs f-col" style="left:403px;top:2690px">
  <h5>QUICK LINKS</h5>
  <ul class="f-links"><li>Home</li><li>About</li><li>Services</li><li>Online Store</li><li>Blog</li><li>Contact</li></ul>
</div>
<div class="abs f-col" style="left:571px;top:2690px">
  <h5>CONTACT US</h5>
  <div class="f-contact">
    <div><svg width="16" height="20" viewBox="0 0 16 20" fill="#fff"><path d="M8 0a7 7 0 0 0-7 7c0 5 7 13 7 13s7-8 7-13a7 7 0 0 0-7-7zm0 10a3 3 0 1 1 0-6 3 3 0 0 1 0 6z"/></svg><span>Lorem ipsum dolor sit amet,<br>consectetur adipiscing</span></div>
    <div><svg width="18" height="18" viewBox="0 0 24 24" fill="#fff"><path d="M5 2h4l2 5-2.5 1.5a11 11 0 0 0 6 6L16 12l5 2v4a2 2 0 0 1-2 2A17 17 0 0 1 3 4a2 2 0 0 1 2-2z"/></svg><span>0455123987</span></div>
    <div><svg width="18" height="14" viewBox="0 0 18 14" fill="#fff"><path d="M0 0h18v2L9 8 0 2zM0 4l9 6 9-6v10H0z"/></svg><span>dan@callowayrecyclers-example.com.au</span></div>
  </div>
</div>
<div class="abs f-col" style="left:863px;top:2690px">
  <h5>NEWSLETTER</h5>
  <div class="newsletter"><span>Enter email</span><b><svg width="16" height="12" viewBox="0 0 18 14" fill="#fff"><path d="M0 0h18v2L9 8 0 2zM0 4l9 6 9-6v10H0z"/></svg></b></div>
  <div class="f-social"><span></span><span></span><span></span><span></span></div>
</div>
<div class="abs copy">©Copyrights 2022 Callowayrecyclers &nbsp;| &nbsp; All Rights Reserved</div>

</body>
</html>
```